American cannabis tech company business card design

Pavrel.com is seeking a modern, professional, and brand-aligned business card that represents our company and its core values: Mission, Story, Values, and Impact. As an innovative cannabis company, we want a business card that is not only visually appealing but also serves as a representation of who we are and what we stand for.

Project Scope: Design a double-sided business card that integrates our brand identity and core values. Incorporate our key brand elements, ensuring a sleek and contemporary aesthetic. Visually reflect our core values (Mission, Story, Values, Impact) in a way that is engaging yet professional.

Target Market(s)

Vendors, third parties,

Contact Information for Business Card

Contact details (name, title, email, phone, website, etc.)

Font styles to use
Other font styles liked:
• Caslon, Centra

Colors

Designer to choose colors to be used in the design.

Requirements
Must have
• Pavrel.com logo and branding A creative yet clean way to integrate our core values (Mission, Story, Values, Impact) Modern typography and a well-structured layout
Nice to have
• forest green, grey, white, black
Should not have
• references to marijuana, leafs, plants, or related product

```html
<!DOCTYPE html>
<html lang="en">
<head>
<meta charset="utf-8">
<title>Pavrel Business Card</title>
<link href="https://fonts.googleapis.com/css2?family=League+Spartan:wght@600;700&family=Outfit:wght@400;600;700&display=swap" rel="stylesheet">
<style>
  :root {
    --backdrop: #969696;
    --card: #fff7ec;
    --forest: #1b3219;
    --divider: #4c5a48;
    --ghost: #fbe8d4;
    --photo-warm: #5a3a2c;
    --photo-olive: #8a8363;
    --photo-moss: #4d5a40;
    --photo-sand: #8b7c66;
  }
  * { margin: 0; padding: 0; box-sizing: border-box; }
  html, body { width: 1200px; height: 1000px; overflow: hidden; }
  body { background: var(--backdrop); position: relative; font-family: "Outfit", sans-serif; color: var(--forest); }

  .card { position: absolute; width: 694px; height: 400px; background: var(--card); border-radius: 24px; overflow: hidden; }
  .card--front { left: 252px; top: 60px; }
  .card--back { left: 253px; top: 490px; }

  .values-block { position: absolute; left: 141px; top: 70px; width: 405px; display: flex; flex-direction: column; gap: 14px; }
  .values-row { display: flex; align-items: center; gap: 12px; height: 55px; }
  .value-word { font-family: "League Spartan", sans-serif; font-weight: 700; font-size: 70px; line-height: 1; padding-top: 10px; white-space: nowrap; flex: none; }
  .photo-slot { flex: 1; height: 54px; border-radius: 4px; }
  .photo-slot--calm { background: linear-gradient(90deg, #2a1a14, var(--photo-warm) 60%, #3a2a22); }
  .photo-slot--friends { background: linear-gradient(90deg, #4d4330, var(--photo-olive) 55%, #b7b49a); }
  .photo-slot--thinker { background: linear-gradient(90deg, var(--photo-moss), #6f6a5a 60%, #2f3a2a); }
  .photo-slot--rest { background: linear-gradient(90deg, #a79d85, var(--photo-sand) 50%, #4c4a3a); }

  .brand-name { position: absolute; left: 60px; top: 168px; font-family: "Outfit", sans-serif; font-weight: 700; font-size: 58px; letter-spacing: 1px; line-height: 1; }
  .divider { position: absolute; left: 346px; top: 101px; width: 2px; height: 197px; background: var(--divider); }
  .contact { position: absolute; left: 390px; top: 107px; }
  .contact-name { font-weight: 700; font-size: 28px; line-height: 1.1; }
  .contact-title { font-size: 18px; line-height: 1.3; }
  .contact-lines { margin-top: 32px; font-size: 17px; line-height: 22px; }
  .contact-web { margin-top: 32px; font-size: 17px; }
  .contact-web strong { font-weight: 700; }
  .ghost-name { position: absolute; left: 452px; top: 298px; font-weight: 700; font-size: 58px; color: var(--ghost); transform: rotate(-8deg); line-height: 1; }
</style>
</head>
<body>
  <section class="card card--front">
    <div class="values-block">
      <div class="values-row">
        <div class="photo-slot photo-slot--calm" role="img" aria-label="Photo of a person relaxing with eyes closed"></div>
        <span class="value-word">MISSION</span>
      </div>
      <div class="values-row">
        <span class="value-word">STORY</span>
        <div class="photo-slot photo-slot--friends" role="img" aria-label="Photo of two friends laughing together"></div>
      </div>
      <div class="values-row">
        <div class="photo-slot photo-slot--thinker" role="img" aria-label="Photo of a man looking up outdoors"></div>
        <span class="value-word">VALUES</span>
      </div>
      <div class="values-row">
        <span class="value-word">IMPACT.</span>
        <div class="photo-slot photo-slot--rest" role="img" aria-label="Photo of a man resting in a hammock with a dog"></div>
      </div>
    </div>
  </section>

  <section class="card card--back">
    <div class="ghost-name" aria-hidden="true">PAVREL</div>
    <div class="brand-name">PAVREL</div>
    <div class="divider"></div>
    <div class="contact">
      <p class="contact-name">Daniel Morrow</p>
      <p class="contact-title">Co-Founder &amp; CEO</p>
      <div class="contact-lines">
        <p>405-555-0148</p>
        <p>name@pavrel.com</p>
      </div>
      <p class="contact-web"><strong>pavrel</strong>.com</p>
    </div>
  </section>
</body>
</html>
```